LHP Regal Business Card Design 2020

Your Manor Steward is looking for a business card that is clean and straight to the point but still looks high-end and attractive. We are a team comprised of management and field professionals focused on the high-end residential marketplace. We serve homeowners and trade professionals directly based out of the Metrowest/Boston area. We provide client services as well as construction/renovation services.
We are aiming for a black and white feel (white background and black text) and a matte finish with rounded edges.

We want to emphasis our vision of "Properties - Projects - Partners".
Dana Pellham is the president of LHP

Please include the following areas we service: Boston/Cape/Newport
Please make sure to include Dana's mobile (555) 213 4480 & office number (555) 640 1937, email dana@yourmanorsteward.example and website www.yourmanorsteward.example

Colors

Designer to choose only greyscale colors for use in the design.

Requirements
Must have
• Include "Properties - Projects - Partners" in design

Include "After Hours Emergency Support # 1800 555 0142" with icon

```html
<!DOCTYPE html>
<html lang="en">
<head>
<meta charset="utf-8">
<title>LHP Business Card</title>
<link rel="stylesheet" href="https://fonts.googleapis.com/css2?family=Montserrat:wght@400;500;600;700;800&display=swap">
<style>
  :root {
    --stage: #1e1e1e;
    --card-dark: #111111;
    --card-light: #ffffff;
    --ink: #2b2b2b;
    --ink-soft: #4a4a4a;
    --paper-text: #f2f2f2;
    --rule: #555555;
  }
  * { box-sizing: border-box; margin: 0; padding: 0; }
  html, body {
    width: 1200px; height: 930px; overflow: hidden;
    background: var(--stage);
    font-family: "Montserrat", sans-serif;
  }
  .canvas { position: relative; width: 1200px; height: 930px; }
  .card {
    position: absolute; width: 600px; height: 345px;
    border-radius: 26px;
    box-shadow: 0 18px 40px rgba(0,0,0,0.55);
    overflow: hidden;
  }
  /* back side */
  .card-back {
    left: 70px; top: 80px;
    background: linear-gradient(135deg, #2a2a2a 0%, var(--card-dark) 55%);
    color: var(--paper-text);
    display: flex; flex-direction: column; align-items: center; justify-content: center;
    text-align: center;
  }
  .wordmark { font-weight: 800; letter-spacing: 2px; line-height: 1; }
  .card-back .wordmark { font-size: 84px; }
  .brand-name { font-weight: 700; letter-spacing: 2px; text-transform: uppercase; }
  .card-back .brand-name { font-size: 17px; margin-top: 8px; }
  .service-title { font-weight: 700; font-size: 17px; letter-spacing: 1.5px; margin-top: 22px; }
  .service-areas { font-weight: 400; font-size: 15.5px; letter-spacing: 1px; margin-top: 8px; }
  .emergency {
    display: flex; align-items: center; gap: 8px;
    margin-top: 18px; font-size: 13px; font-weight: 500; letter-spacing: 0.5px;
  }
  .emergency svg { width: 14px; height: 14px; flex: none; }
  /* front side */
  .card-front {
    left: 530px; top: 500px;
    background: var(--card-light);
    color: var(--ink);
  }
  .front-brand {
    position: absolute; left: 30px; top: 92px; width: 240px;
    text-align: center;
  }
  .card-front .wordmark { font-size: 78px; color: var(--ink); }
  .card-front .brand-name { font-size: 13px; margin-top: 8px; color: var(--ink); }
  .divider {
    position: absolute; left: 284px; top: 60px; width: 1px; height: 150px;
    background: var(--rule);
  }
  .contact { position: absolute; left: 304px; top: 58px; }
  .person-name { font-weight: 700; font-size: 21px; letter-spacing: 1px; }
  .person-role { font-weight: 400; font-size: 14px; color: var(--ink-soft); margin-top: 2px; margin-left: 18px; }
  .contact-list { list-style: none; margin-top: 12px; margin-left: 18px; }
  .contact-list li {
    display: flex; align-items: center; gap: 7px;
    font-size: 13px; color: var(--ink); line-height: 20px; white-space: nowrap;
  }
  .contact-list svg { width: 11px; height: 11px; flex: none; }
  .vision {
    position: absolute; left: 0; right: 0; bottom: 52px;
    text-align: center; font-weight: 600; font-size: 21px; letter-spacing: 1px;
    color: var(--ink);
  }
</style>
</head>
<body>
<main class="canvas">
  <section class="card card-back" aria-label="Card back">
    <div class="wordmark">LHP</div>
    <div class="brand-name">Your Manor Steward</div>
    <div class="service-title">WE SERVICE</div>
    <div class="service-areas">BOSTON | METROWEST | SOUTH SHORE | CAPE/NEWPORT</div>
    <div class="emergency">
      <svg viewBox="0 0 12 12" aria-hidden="true"><path d="M2.5 1 L4.5 1 L5 3.5 L3.8 4.4 Q4.8 6.8 7.6 8.2 L8.5 7 L11 7.5 L11 9.5 Q10.5 11 9 11 Q1 9.5 1 3 Q1 1.5 2.5 1 Z" fill="#f2f2f2"/></svg>
      After Hours Emergency Support # 1800 555 0142
    </div>
  </section>

  <section class="card card-front" aria-label="Card front">
    <div class="front-brand">
      <div class="wordmark">LHP</div>
      <div class="brand-name">Your Manor Steward</div>
    </div>
    <div class="divider"></div>
    <div class="contact">
      <div class="person-name">DANA PELLHAM</div>
      <div class="person-role">President</div>
      <ul class="contact-list">
        <li>
          <svg viewBox="0 0 12 12" aria-hidden="true"><path d="M2.5 1 L4.5 1 L5 3.5 L3.8 4.4 Q4.8 6.8 7.6 8.2 L8.5 7 L11 7.5 L11 9.5 Q10.5 11 9 11 Q1 9.5 1 3 Q1 1.5 2.5 1 Z" fill="#2b2b2b"/></svg>
          (555) 640 1937
        </li>
        <li>
          <svg viewBox="0 0 12 12" aria-hidden="true"><rect x="3" y="0.8" width="6" height="10.4" rx="1.2" fill="none" stroke="#2b2b2b" stroke-width="1.3"/><circle cx="6" cy="9.3" r="0.7" fill="#2b2b2b"/></svg>
          (555) 213 4480
        </li>
        <li>
          <svg viewBox="0 0 12 12" aria-hidden="true"><rect x="0.8" y="2.3" width="10.4" height="7.4" rx="1" fill="none" stroke="#2b2b2b" stroke-width="1.2"/><path d="M1 2.8 L6 6.6 L11 2.8" fill="none" stroke="#2b2b2b" stroke-width="1.2"/></svg>
          dana@yourmanorsteward.example
        </li>
        <li>
          <svg viewBox="0 0 12 12" aria-hidden="true"><circle cx="6" cy="6" r="5" fill="none" stroke="#2b2b2b" stroke-width="1.1"/><ellipse cx="6" cy="6" rx="2.2" ry="5" fill="none" stroke="#2b2b2b" stroke-width="1"/><path d="M1 6 H11 M2 3.5 H10 M2 8.5 H10" stroke="#2b2b2b" stroke-width="0.9"/></svg>
          www.yourmanorsteward.example
        </li>
      </ul>
    </div>
    <div class="vision">PROPERTIES - PROJECTS - PARTNERS</div>
  </section>
</main>
</body>
</html>
```